Professional, Attractive, Simple Website Needed!!

We completed the design for our logo.

We need a website built out around this.

Here are a couple samples of how we want ours formatted.

http://brimvoltco.com

http://www.ravelbeam.com/lp/free-quote?LeadSource=Search%20Engine&ProgramName=searchads&experience=qual&language=en&type=brd&gclid=Xk7PLmqwTRZBNVuEYcaHdFgWsLoPeRtQnMxVbCzJaKiOuYtReWqAsDfGhJkLzXcVbNmQwErTyUiOpAsDfGhJkLzX_wcB

http://quorel.co
Updates

Project Deadline Extended
Reason: Extending this deadline due to our delay in providing designers with content for each page. This is coming in next 24 hours.

Project Deadline Extended
Reason: Due to scheduling conflicts and extended travel delays related to Puerto Rico, the deadline has been extended. Your patience is greatly appreciated.

Project Deadline Extended
Reason: Travel and scheduling conflicts have made it impossible to give this project the thorough review it deserves, therefore I am extending the deadline. Thank you for your patience!

Target Market(s)

Home Owners who earn 60k + household annually

Industry/Entity Type

It Professional

Coding

Coded - Design and coding required

Number of Pages Required

5+ page

Font styles to use
Serif

Colors
34a7d8
9bcb3c

Requirements
Must have
• Simple
• Lead form Entry (Ability for visitor to enter Name, number and address for a quote)
• Sleek Design
• Professional
• Testimonials
• Use color Scheme of Design Logo Attached
Nice to have
• Video when site starts
• Like this
• https://www.vidplexa.com/watch?v=Qm8rTbLw3Np&feature=vidplexa.be
Should not have
• Should not include Commercial solar
• Should not include wind power

```html
<!DOCTYPE html>
<html lang="en">
<head>
<meta charset="utf-8">
<title>Sunvale Power</title>
<link href="https://fonts.googleapis.com/css2?family=Hind:wght@400;500;600;700&family=Roboto:wght@400;700&display=swap" rel="stylesheet">
<style>
:root{
  --green:#8cc63f;
  --green-dark:#5ab435;
  --yellow:#f5ec00;
  --blue:#1587d4;
  --ink:#333;
  --muted:#666;
  --footer:#262a33;
  --footer-line:#3c414b;
  --footer-text:#8a8f98;
  --white:#fff;
}
*{box-sizing:border-box;margin:0;padding:0}
html,body{width:746px;height:1200px;overflow:hidden;background:var(--white)}
body{position:relative;font-family:"Hind",sans-serif;color:var(--ink)}
.hero{position:absolute;left:0;top:0;width:746px;height:420px;
  background:linear-gradient(180deg,#1d2a3c 0%,#3d5f86 22%,#6f8fae 38%,#2f4d7e 60%,#28407a 100%)}
.hero-curve{position:absolute;left:0;top:330px;width:746px;height:100px}
.brand{position:absolute;left:52px;top:30px;display:flex;align-items:center;gap:6px;color:var(--white);font-weight:700;font-size:15px}
.brand-dot{width:12px;height:12px;border-radius:50%;background:var(--green)}
.nav{position:absolute;top:33px;left:259px;display:flex;align-items:center;font-size:8.5px;font-weight:500;color:var(--white);letter-spacing:.2px}
.nav a{color:inherit;text-decoration:none;padding:6px 9px;margin-right:4px}
.nav a.active{background:var(--green);padding:6px 10px}
.nav a.last{margin-left:10px}
.hero-kicker{position:absolute;top:112px;width:100%;text-align:center;color:var(--white);font-size:13px;font-weight:500}
.hero-title{position:absolute;top:128px;width:100%;text-align:center;color:var(--white);font-size:33px;font-weight:700;letter-spacing:.3px}
.zip-box{position:absolute;left:270px;top:265px;width:237px;height:188px;background:rgba(30,30,30,.85);border-radius:2px;text-align:center;padding-top:24px}
.zip-box h2{color:var(--white);font-size:12.5px;font-weight:500;line-height:18px;letter-spacing:.2px}
.zip-input{display:block;margin:16px auto 0;width:160px;height:30px;background:var(--white);border:0}
.zip-btn{display:block;margin:11px auto 0;width:160px;height:30px;background:var(--green);color:#222;font-family:inherit;font-size:11.5px;font-weight:500;border:0;line-height:32px}
.steps-intro{position:absolute;top:516px;width:100%;text-align:center}
.steps-intro h2{font-size:18.5px;font-weight:500;letter-spacing:.4px;color:#222}
.steps-intro p{width:470px;margin:10px auto 0;font-size:9px;line-height:14px;color:var(--muted)}
.steps{position:absolute;top:660px;left:0;width:746px;height:160px}
.step{position:absolute;width:120px;text-align:center}
.step svg{display:block;margin:0 auto}
.step p{font-size:8px;line-height:10px;color:#777;margin-top:4px}
.footer{position:absolute;left:0;top:918px;width:746px;height:282px;background:var(--footer);font-family:"Roboto",sans-serif;color:var(--footer-text);font-size:7.5px}
.f-brand{position:absolute;left:61px;top:40px;display:flex;align-items:center;gap:6px;color:var(--green);font-family:"Hind",sans-serif;font-weight:700;font-size:15px}
.f-about{position:absolute;left:61px;top:94px;width:135px;line-height:16px}
.social{position:absolute;left:61px;top:178px;display:flex;gap:5px}
.social span{width:21px;height:21px;border-radius:50%;background:#363b45;display:block}
.contacts{position:absolute;left:216px;top:30px;width:453px;height:47px;border-bottom:1px solid var(--footer-line)}
.contact{position:absolute;top:0;display:flex;gap:8px;line-height:13px}
.contact i{width:20px;height:20px;border-radius:50%;background:#363b45;display:flex;align-items:center;justify-content:center;flex:none}
.col{position:absolute;top:98px}
.col h3{color:var(--white);font-size:8.5px;font-weight:700;margin-bottom:16px}
.col li{list-style:none;line-height:19px;font-size:8px}
.col li:before{content:"";display:inline-block;width:3px;height:3px;border-radius:50%;background:var(--footer-text);margin-right:7px;vertical-align:middle}
.newsletter p{width:140px;line-height:16px}
.nl-email{margin-top:17px;width:140px;height:22px;background:#3a3f48;padding-left:8px;line-height:22px;font-size:6.5px}
.nl-btn{margin-top:6px;width:140px;height:22px;background:var(--blue);color:var(--white);text-align:center;line-height:22px;font-weight:700;font-size:7px}
.copy{position:absolute;left:61px;top:245px;width:608px;border-top:1px solid var(--footer-line);text-align:center;padding-top:12px;font-size:7px}
</style>
</head>
<body>
<header class="hero" role="img" aria-label="Worker in a safety vest installing rooftop solar panels under a blue sky"></header>
<svg class="hero-curve" viewBox="0 0 746 100" preserveAspectRatio="none" aria-hidden="true">
  <path d="M0 25 Q120 80 373 86 Q600 88 746 70 L746 100 L0 100 Z" fill="#fff"/>
</svg>
<div class="brand"><span class="brand-dot"></span>Sunvale Power</div>
<nav class="nav">
  <a class="active">HOME</a><a>WHY</a><a>PARTNERSHIPS</a><a>QUOREL FOUNDATION</a><a>BLOG</a><a>FAQ</a><a class="last">CONTACT US</a>
</nav>
<p class="hero-kicker">With Best Quality Solar Reception Cells</p>
<h1 class="hero-title">Sunvale Power</h1>
<section class="zip-box">
  <h2>ENTER YOUR ZIP CODE TO SEE<br>IF SOLAR WORKS FOR YOU.</h2>
  <div class="zip-input"></div>
  <div class="zip-btn">Get Started</div>
</section>

<section class="steps-intro">
  <h2>4 EASY STEPS TO GOING SOLAR</h2>
  <p>The world as it is heavily dependant on petrol, coal, wood and water for producing energy. We assume there is uninterrupted supply. There is n't! On the other hand, we have inexhaustible supply of solar energy. So why not rely more on solar energy ?</p>
</section>

<section class="steps">
  <div class="step" style="left:46px">
    <svg width="110" height="130" viewBox="0 0 110 130">
      <path d="M55 112 L40 95 A48 48 0 1 1 70 95 Z" fill="var(--green-dark)"/>
      <circle cx="55" cy="50" r="40" fill="var(--yellow)"/><circle cx="55" cy="50" r="35" fill="var(--green-dark)"/>
      <g fill="none" stroke="#fff" stroke-width="1.5"><path d="M38 54 V48 A17 17 0 0 1 72 48 V54"/><rect x="34" y="48" width="7" height="12" rx="3"/><rect x="69" y="48" width="7" height="12" rx="3"/><path d="M72 60 Q70 68 58 68"/></g>
      <circle cx="55" cy="118" r="2" fill="var(--green-dark)"/><circle cx="55" cy="126" r="2" fill="var(--green-dark)"/>
      <circle cx="90" cy="20" r="12" fill="var(--blue)" stroke="#fff" stroke-width="2"/><text x="90" y="25" text-anchor="middle" fill="#fff" font-family="Hind,sans-serif" font-weight="700" font-size="14">1</text>
    </svg>
    <p>Speak to a<br>solar consultant</p>
  </div>
  <div class="step" style="left:223px">
    <svg width="110" height="130" viewBox="0 0 110 130">
      <path d="M55 112 L40 95 A48 48 0 1 1 70 95 Z" fill="var(--green-dark)"/>
      <circle cx="55" cy="50" r="40" fill="var(--yellow)"/><circle cx="55" cy="50" r="35" fill="var(--green-dark)"/>
      <g fill="none" stroke="#fff" stroke-width="1.5"><path d="M42 38 H68 L76 60 H34 Z"/><path d="M55 38 V60 M38 49 H72 M48 38 L45 60 M62 38 L65 60"/></g>
      <circle cx="55" cy="118" r="2" fill="var(--green-dark)"/><circle cx="55" cy="126" r="2" fill="var(--green-dark)"/>
      <circle cx="90" cy="20" r="12" fill="var(--blue)" stroke="#fff" stroke-width="2"/><text x="90" y="25" text-anchor="middle" fill="#fff" font-family="Hind,sans-serif" font-weight="700" font-size="14">2</text>
    </svg>
    <p>We'll design your<br>solar panel system</p>
  </div>
  <div class="step" style="left:392px">
    <svg width="110" height="130" viewBox="0 0 110 130">
      <path d="M55 112 L40 95 A48 48 0 1 1 70 95 Z" fill="var(--green-dark)"/>
      <circle cx="55" cy="50" r="40" fill="var(--yellow)"/><circle cx="55" cy="50" r="35" fill="var(--green-dark)"/>
      <g fill="none" stroke="#fff" stroke-width="1.5"><rect x="39" y="36" width="32" height="28" rx="2"/><path d="M39 44 H71 M45 32 V39 M65 32 V39 M44 50 H48 M53 50 H57 M62 50 H66 M44 57 H48 M53 57 H57 M61 57 L63 59 L67 54"/></g>
      <circle cx="55" cy="118" r="2" fill="var(--green-dark)"/><circle cx="55" cy="126" r="2" fill="var(--green-dark)"/>
      <circle cx="90" cy="20" r="12" fill="var(--blue)" stroke="#fff" stroke-width="2"/><text x="90" y="25" text-anchor="middle" fill="#fff" font-family="Hind,sans-serif" font-weight="700" font-size="14">3</text>
    </svg>
    <p>Schedule your<br>1 day install</p>
  </div>
  <div class="step" style="left:559px">
    <svg width="110" height="130" viewBox="0 0 110 130">
      <path d="M55 112 L40 95 A48 48 0 1 1 70 95 Z" fill="var(--green-dark)"/>
      <circle cx="55" cy="50" r="40" fill="var(--yellow)"/><circle cx="55" cy="50" r="35" fill="var(--green-dark)"/>
      <g fill="none" stroke="#fff" stroke-width="1.5"><circle cx="55" cy="52" r="14"/><path d="M59 46 H53 A3 3 0 0 0 53 52 H57 A3 3 0 0 1 57 58 H51 M55 43 V61"/></g>
      <circle cx="55" cy="118" r="2" fill="var(--green-dark)"/><circle cx="55" cy="126" r="2" fill="var(--green-dark)"/>
      <circle cx="90" cy="20" r="12" fill="var(--blue)" stroke="#fff" stroke-width="2"/><text x="90" y="25" text-anchor="middle" fill="#fff" font-family="Hind,sans-serif" font-weight="700" font-size="14">4</text>
    </svg>
    <p>Start saving on your<br>electricity bill</p>
  </div>
</section>

<footer class="footer">
  <div class="f-brand"><span class="brand-dot"></span>Sunvale Power</div>
  <p class="f-about">We are Lumera, we industry factory company and provide you the best service and support comes register to receive service information</p>
  <div class="social"><span></span><span></span><span></span><span></span><span></span></div>
  <div class="contacts">
    <div class="contact" style="left:0"><i><svg width="9" height="10" viewBox="0 0 9 10"><path d="M4.5 9.5 C1 5.5 1 4.5 1 3.5 A3.5 3.5 0 0 1 8 3.5 C8 4.5 8 5.5 4.5 9.5 Z" fill="none" stroke="#aaa"/><circle cx="4.5" cy="3.5" r="1.2" fill="#aaa"/></svg></i><span>42 Larkspur Lane - Westfield<br>Grove</span></div>
    <div class="contact" style="left:150px"><i><svg width="9" height="9" viewBox="0 0 9 9"><path d="M1 1.5 L3 1 L4 3 L3 4 Q4 6 5 6 L6 5 L8 6 L7.5 8 Q2 8 1 1.5 Z" fill="none" stroke="#aaa" stroke-width=".8"/></svg></i><span>(+10) 0555 210 734<br>(05) 555 8142 07</span></div>
    <div class="contact" style="left:302px"><i><svg width="9" height="7" viewBox="0 0 9 7"><rect x=".5" y=".5" width="8" height="6" fill="none" stroke="#aaa" stroke-width=".8"/><path d="M.5 .5 L4.5 4 L8.5 .5" fill="none" stroke="#aaa" stroke-width=".8"/></svg></i><span style="line-height:20px">info@sunvalemail.com</span></div>
  </div>
  <div class="col" style="left:216px"><h3>QUICKLINK</h3><ul><li>Clean Energy</li><li>Solar Power</li><li>Repair Turbine</li><li>Energy Research</li></ul></div>
  <div class="col" style="left:372px"><h3>CUSTOMER CARE</h3><ul><li>Customer Service</li><li>Warranty Policy</li><li>Installation and Use</li><li>Contact Us</li></ul></div>
  <div class="col newsletter" style="left:528px"><h3>NEWSLETTER</h3><p>Sign up for our newsletter and follow us on social media</p><div class="nl-email">Email</div><div class="nl-btn">SUBSCRIBE</div></div>
  <p class="copy">Copyright © 2017 Sunvale Power.&nbsp; All rights reserved.</p>
</footer>
</body>
</html>
```